Web site for small printshop

I am looking for a website for small printshop in Iceland, mainly serving university students and artist.

We print posters, flyers, business cards and more.

In addition to our current website, I would like to include design tool, (fx. www.quarvelpad.example, www.trindomap.example or something similar) jobs upload, shopping chart.
Updates

Great work, I am really amazed of the quality of work i am seeing here.

Really way beyond my expectation

GOOD JOB - all of you ! 

Hi all.

The designs submitted have been great, way better than expected.
I really did not expect this level of quality.

Some have been asking me for feedback on their designs, and I will try 
to send some feedback here, without spoiling your creativity.

Likes:
- when the colors of my logo is used in menus, buttons etc.
- simple, not to crowded look.

Dislikes.
- Dark and heavy design
- Lot of text and buttons (crowded look)

Extra info.
- top line (before menus) will contain: Tel - email - language
- menu line will have 5 categories: Home - service - submission of works - FAQ - about us
- 3 large buttons:  Job submit - Job design - ask for offer

LOVE YOUR WORK - great designs so far :)

Target Market(s)

University Students, Artists. Age group 20-30

Industry/Entity Type

University

Requirements
Must have
• The website must be easy to use, clean looking.

```html
<!DOCTYPE html>
<html lang="en">
<head>
<meta charset="utf-8">
<title>Arkahús – Print shop</title>
<link rel="stylesheet" href="https://fonts.googleapis.com/css2?family=Open+Sans:wght@400;600;700&family=Oswald:wght@300&display=swap">
<style>
  :root {
    --red: #ef4036;
    --yellow: #fded2a;
    --green: #80c242;
    --mail-green: #3aa935;
    --ink: #2a2a2a;
    --nav: #555555;
    --muted: #7a7a7a;
    --topbar: #f5f5f5;
    --band: #e3e3e3;
    --line: #dcdcdc;
    --white: #ffffff;
  }
  * { box-sizing: border-box; margin: 0; padding: 0; }
  html, body { width: 1200px; height: 900px; overflow: hidden; background: var(--white); }
  body { position: relative; font-family: "Open Sans", Arial, sans-serif; color: var(--ink); }

  .topbar { position: absolute; left: 0; top: 0; width: 1200px; height: 34px; background: var(--topbar); }
  .topbar-list { position: absolute; right: 101px; top: 7px; display: flex; font-size: 13px; font-weight: 700; line-height: 18px; list-style: none; white-space: nowrap; }
  .topbar-list li { padding: 0 8px; border-left: 2px solid #333; }
  .topbar-list li:first-child { border-left: none; }
  .topbar-list li:last-child { padding-right: 0; }
  .topbar-call { color: var(--red); }
  .topbar-mail { color: var(--mail-green); }
  .topbar-lang { color: var(--muted); }

  .site-header { position: absolute; left: 0; top: 34px; width: 1200px; height: 78px; border-bottom: 1px solid var(--line); }
  .brand { position: absolute; left: 98px; top: 20px; display: flex; align-items: center; gap: 12px; }
  .brand-mark { width: 30px; height: 30px; border-radius: 50%; background: var(--red); }
  .brand-name { font-size: 28px; font-weight: 600; color: var(--ink); }
  .main-nav { position: absolute; top: 26px; left: 0; width: 1200px; font-size: 16.5px; font-weight: 700; color: var(--nav); }
  .main-nav a { position: absolute; color: inherit; text-decoration: none; white-space: nowrap; }

  .hero-title { position: absolute; left: 100px; top: 227px; font-family: "Oswald", "Arial Narrow", sans-serif; font-weight: 300; font-size: 40px; letter-spacing: -0.3px; line-height: 46px; color: #555; white-space: nowrap; }
  .action { position: absolute; top: 366px; width: 160px; text-align: center; text-decoration: none; color: var(--ink); }
  .action-circle { display: block; width: 118px; height: 118px; margin: 0 auto; border-radius: 50%; }
  .action-circle svg { display: block; }
  .action-label { display: block; margin-top: 16px; font-size: 16px; font-weight: 600; white-space: nowrap; }
  .action--submit .action-circle { background: var(--red); }
  .action--design .action-circle { background: var(--yellow); }
  .action--offer .action-circle { background: var(--green); }

  .hero-photo { position: absolute; left: 612px; top: 126px; width: 494px; height: 466px;
    background: radial-gradient(ellipse at 55% 45%, #d8c7b4 0%, #b9c6d4 40%, #f2f2f2 75%, #ffffff 100%); border-radius: 40px; }

  .products-band { position: absolute; left: 0; top: 594px; width: 1200px; height: 288px; background: var(--band); }
  .products-card { position: absolute; left: 100px; top: 32px; width: 1000px; height: 224px; background: var(--white); border-radius: 4px; }
  .products-frame { position: absolute; left: 10px; top: 10px; width: 979px; height: 203px; border: 1px solid var(--line); border-radius: 6px; }
  .product { position: absolute; top: 17px; width: 161px; text-align: center; }
  .product-title { display: block; font-size: 15px; color: var(--red); line-height: 20px; height: 35px; margin: 0 -20px; white-space: nowrap; }
  .product-image { display: block; width: 161px; height: 108px; }
  .product-price { display: block; margin-top: 12px; font-size: 12px; font-weight: 700; color: #444; white-space: nowrap; }
  .img-labels { background: linear-gradient(135deg, #e9e4dc, #bfb6a8 60%, #3a2d22); }
  .img-postcards { background: linear-gradient(90deg, #d9d9d9, #eeeeee 50%, #e6753a 75%, #4ab3d6); }
  .img-magnets { background: linear-gradient(120deg, #a9cf3d, #e7ecd5 45%, #e8483a 70%, #2e2e2e); }
  .img-signage { background: linear-gradient(135deg, #f4f4f4, #d9d9d9 50%, #3fb24a 70%, #7a4a9a); }
  .img-cards { background: linear-gradient(135deg, #e9e4dc, #bfb6a8 60%, #3a2d22); }

  .slider-arrow { position: absolute; top: 120px; }
  .slider-arrow--prev { left: 56px; }
  .slider-arrow--next { left: 1120px; }

  .footer-accent { position: absolute; left: 819px; top: 895px; width: 281px; height: 5px; background: var(--red); }
</style>
</head>
<body>

<div class="topbar">
  <ul class="topbar-list">
    <li class="topbar-call">CALL US &nbsp;: 09 7654321</li>
    <li class="topbar-mail">Mailto : info@arkahus.example</li>
    <li class="topbar-lang">Language: English</li>
  </ul>
</div>

<header class="site-header">
  <div class="brand">
    <span class="brand-mark"></span>
    <span class="brand-name">Arkahús</span>
  </div>
  <nav class="main-nav">
    <a href="#" style="left:595px">Home</a>
    <a href="#" style="left:693px">Services</a>
    <a href="#" style="left:811px">Submit Works</a>
    <a href="#" style="left:960px">FAQ</a>
    <a href="#" style="left:1027px">About us</a>
  </nav>
</header>

<h1 class="hero-title">Want to reduce your print costs<br>and Productivity ?</h1>

<a href="#" class="action action--submit" style="left:79px">
  <span class="action-circle">
    <svg width="118" height="118" viewBox="0 0 118 118">
      <rect x="34" y="41" width="50" height="38" rx="3" fill="#fff"/>
      <path d="M50 41v-5h18v5" fill="none" stroke="#fff" stroke-width="4"/>
    </svg>
  </span>
  <span class="action-label">JOB SUBMIT</span>
</a>
<a href="#" class="action action--design" style="left:220px">
  <span class="action-circle">
    <svg width="118" height="118" viewBox="0 0 118 118">
      <path d="M32 60c0-14 14-22 28-21 15 1 26 10 26 20 0 6-5 8-11 7-5-1-8 2-6 7 2 6-4 9-11 9-15 0-26-9-26-22z" fill="#4a4a4a"/>
      <circle cx="46" cy="56" r="3.5" fill="#fded2a"/>
      <circle cx="58" cy="48" r="3.5" fill="#fded2a"/>
      <circle cx="72" cy="52" r="3.5" fill="#fded2a"/>
      <circle cx="46" cy="68" r="3.5" fill="#fded2a"/>
      <circle cx="58" cy="72" r="3.5" fill="#fded2a"/>
    </svg>
  </span>
  <span class="action-label">JOB DESIGN</span>
</a>
<a href="#" class="action action--offer" style="left:373px">
  <span class="action-circle">
    <svg width="118" height="118" viewBox="0 0 118 118">
      <text x="59" y="82" text-anchor="middle" font-family="Open Sans, Arial, sans-serif" font-weight="700" font-size="66" fill="#fff">?</text>
    </svg>
  </span>
  <span class="action-label" style="margin-left:12px">ASK FOR OFFER</span>
</a>

<div class="hero-photo" role="img" aria-label="Photo of four cheerful students holding up folders and notebooks"></div>

<section class="products-band">
  <svg class="slider-arrow slider-arrow--prev" width="26" height="30" viewBox="0 0 26 30" aria-label="Previous">
    <path d="M20 2L6 15l14 13" fill="none" stroke="#e8392f" stroke-width="7"/>
  </svg>
  <div class="products-card">
    <div class="products-frame">
      <div class="product" style="left:18px">
        <span class="product-title">Adhessive Labes</span>
        <span class="product-image img-labels" role="img" aria-label="Photo of printed adhesive labels"></span>
        <span class="product-price">100 (55x90 ) - $55</span>
      </div>
      <div class="product" style="left:213px">
        <span class="product-title">Post cards</span>
        <span class="product-image img-postcards" role="img" aria-label="Photo of printed post cards"></span>
        <span class="product-price">100 colur - $25</span>
      </div>
      <div class="product" style="left:408px">
        <span class="product-title">Magnetics stickers</span>
        <span class="product-image img-magnets" role="img" aria-label="Photo of printed magnetic stickers"></span>
        <span class="product-price">From $20</span>
      </div>
      <div class="product" style="left:600px">
        <span class="product-title">Signage</span>
        <span class="product-image img-signage" role="img" aria-label="Photo of a printed signage brochure"></span>
        <span class="product-price">From $50</span>
      </div>
      <div class="product" style="left:791px">
        <span class="product-title">Businees cards</span>
        <span class="product-image img-cards" role="img" aria-label="Photo of printed business cards"></span>
        <span class="product-price">ADD PRICE</span>
      </div>
    </div>
  </div>
  <svg class="slider-arrow slider-arrow--next" width="26" height="30" viewBox="0 0 26 30" aria-label="Next">
    <path d="M6 2l14 13L6 28" fill="none" stroke="#e8392f" stroke-width="7"/>
  </svg>
</section>

<div class="footer-accent"></div>

</body>
</html>
```